Business Card for my New Brokerage

Looking to get a business card design for my new Real Estate Brokerage.
I want it with Picture, Phone Number, Email, Website, Office Address
Name and Designation. Please add logo too.

Target Market(s)

Real Estate Investors or Home Buyers

Industry/Entity Type

Real Estate

Contact Information for Business Card

Name, Email, Phone Number, website, email, office address

Colors
EB3D1F
EC4F4E
F09395
F8D3D4
FCEDEE

Requirements
Must have
• Minimalistic, Clean, Modern, Photo
Nice to have
• White and Red Colors

```html
<!DOCTYPE html>
<html lang="en">
<head>
<meta charset="utf-8">
<title>Ember Realty Inc – Business Card</title>
<link href="https://fonts.googleapis.com/css2?family=Montserrat:wght@400;500;700;800&display=swap" rel="stylesheet">
<style>
  :root {
    --stage: #1e1e1e;
    --red: #dd0000;
    --gold: #c9a04a;
    --white: #ffffff;
    --ink: #3a3a3a;
    --card-w: 600px;
    --card-h: 343px;
  }
  * { box-sizing: border-box; margin: 0; padding: 0; }
  html, body {
    width: 1200px; height: 1015px; overflow: hidden;
    background: var(--stage);
    font-family: "Montserrat", sans-serif;
  }
  .stage {
    width: 1200px; height: 1015px;
    display: flex; flex-direction: column; align-items: center; justify-content: center;
    gap: 60px;
  }
  .card {
    position: relative;
    width: var(--card-w); height: var(--card-h);
    border-radius: 26px;
    overflow: hidden;
    box-shadow: 0 14px 30px rgba(0,0,0,.55);
  }

  /* Front */
  .card--front {
    background: linear-gradient(200deg, #c9a04a 0%, #d1441c 22%, var(--red) 42%, var(--red) 100%);
    display: flex; align-items: center; justify-content: center;
  }
  .brand {
    display: flex; align-items: center; gap: 10px;
    font-weight: 800; font-size: 44px; letter-spacing: 2px;
    text-transform: uppercase;
    line-height: 1;
  }
  .brand__mark { width: 12px; height: 12px; }
  .card--front .brand { color: var(--white); }
  .card--front .brand__mark { background: var(--white); }

  /* Back */
  .card--back { background: var(--white); }
  .card--back .brand {
    position: absolute; top: 70px; left: 0; right: 0; justify-content: center;
    color: var(--red);
  }
  .card--back .brand__mark { background: var(--red); }
  .info-band {
    position: absolute; left: 0; right: 0; top: 176px; height: 100px;
    background: var(--red);
    border-top: 3px solid var(--gold);
    border-bottom: 3px solid var(--gold);
    display: flex; align-items: center;
    color: var(--white);
  }
  .person {
    width: 290px; text-align: right; padding-right: 26px;
    border-right: 1px solid rgba(255,255,255,.75);
    height: 60px; display: flex; flex-direction: column; justify-content: center;
  }
  .person__name { font-weight: 700; font-size: 20px; letter-spacing: .3px; }
  .person__role { font-weight: 400; font-size: 14px; margin-top: 2px; }
  .contacts { list-style: none; padding-left: 24px; font-size: 14px; font-weight: 500; }
  .contacts li { display: flex; align-items: center; gap: 8px; line-height: 22px; }
  .contacts svg { width: 14px; height: 14px; fill: none; stroke: var(--white); stroke-width: 1.6; }
  .address {
    position: absolute; left: 0; right: 0; top: 300px;
    text-align: center; font-size: 14px; color: var(--ink); font-weight: 500;
  }
</style>
</head>
<body>
<main class="stage">
  <section class="card card--front" aria-label="Card front">
    <div class="brand">Ember Realty Inc<span class="brand__mark"></span></div>
  </section>

  <section class="card card--back" aria-label="Card back">
    <div class="brand">Ember Realty Inc<span class="brand__mark"></span></div>
    <div class="info-band">
      <div class="person">
        <p class="person__name">DANIEL HARPER</p>
        <p class="person__role">Managing Director</p>
      </div>
      <ul class="contacts">
        <li>
          <svg viewBox="0 0 16 16" aria-hidden="true"><path d="M4 1.5l2.2 3-1.4 1.6a8 8 0 0 0 5.1 5.1l1.6-1.4 3 2.2-1.3 2.3C7.5 14.3 1.7 8.5 1.7 2.8z"/></svg>
          021-555 010 234
        </li>
        <li>
          <svg viewBox="0 0 16 16" aria-hidden="true"><rect x="1.5" y="3.5" width="13" height="9"/><path d="M1.5 3.5l6.5 5 6.5-5"/></svg>
          info@emberrealty.com
        </li>
        <li>
          <svg viewBox="0 0 16 16" aria-hidden="true"><circle cx="8" cy="8" r="6.5"/><ellipse cx="8" cy="8" rx="2.8" ry="6.5"/><path d="M1.5 8h13"/></svg>
          www.emberrealty.com
        </li>
      </ul>
    </div>
    <p class="address">88, Linden Avenue, Suite 4 70318, Westland</p>
  </section>
</main>
</body>
</html>
```